New Business Card Design Project

I'd like a business card design around the same modern style that I used on my website www.brovanhs.com
It's gonna be one of those round corners double-sided business cards with maybe a big logo on the front and all the info on the back of the card.

Contact Information for Business Card

Marco Delgado
425-317-6084
www.brovanhs.com

www.friendlane.com/BrovanHomeServices
www.picstream.com/BrovanHomeServices

Requirements
Must have
• it needs to look elegant and modern

```html
<!DOCTYPE html>
<html lang="en">
<head>
<meta charset="utf-8">
<title>Brovan Home Services – Business Card</title>
<link rel="stylesheet" href="https://fonts.googleapis.com/css2?family=Montserrat:wght@400;500;700;800&display=swap">
<style>
  :root {
    --stage: #1c1d20;
    --card: #26292d;
    --card-edge: #2e3136;
    --blue: #1ba6ec;
    --white: #f4f6f8;
    --muted: #d9dde2;
  }
  * { box-sizing: border-box; margin: 0; padding: 0; }
  html, body {
    width: 1200px; height: 800px; overflow: hidden;
    background: var(--stage);
    font-family: "Montserrat", sans-serif;
  }
  .canvas { position: relative; width: 1200px; height: 800px; }

  .card {
    position: absolute;
    width: 520px; height: 300px;
    background: var(--card);
    border: 1px solid var(--card-edge);
    border-radius: 14px;
    overflow: hidden;
    box-shadow: 0 18px 40px rgba(0,0,0,.55);
  }
  .card--front { left: 70px; top: 110px; }
  .card--back  { left: 610px; top: 390px; }

  /* Front */
  .card--front .brand {
    position: absolute; inset: 0;
    display: flex; align-items: center; justify-content: center;
    padding: 0 40px;
  }
  .brand-name {
    color: var(--blue);
    font-weight: 800;
    text-align: center;
    line-height: 1.05;
  }
  .card--front .brand-name { font-size: 48px; letter-spacing: -0.5px; }

  /* Back */
  .card--back .brand {
    position: absolute; left: 0; right: 0; top: 50px;
    display: flex; justify-content: center;
  }
  .card--back .brand-name { font-size: 32px; letter-spacing: -0.3px; }

  .divider {
    position: absolute; left: 0; right: 0; top: 124px;
    display: flex; align-items: center; gap: 14px;
  }
  .divider .rule { flex: 1; height: 1px; background: var(--blue); }
  .person-name {
    color: var(--white); font-weight: 700; font-size: 16px;
    white-space: nowrap;
  }

  .contact {
    position: absolute; left: 0; right: 0; top: 150px;
    list-style: none; text-align: center;
    color: var(--muted); font-size: 12.5px; font-weight: 500;
    line-height: 1.65;
  }
  .contact .accent { color: var(--blue); }

  .base-band {
    position: absolute; left: 0; right: 0; bottom: 0;
    height: 9px; background: var(--blue);
  }
</style>
</head>
<body>
<main class="canvas">

  <section class="card card--front" aria-label="Card front">
    <div class="brand">
      <p class="brand-name">Brovan Home Services</p>
    </div>
  </section>

  <section class="card card--back" aria-label="Card back">
    <div class="brand">
      <p class="brand-name">Brovan Home Services</p>
    </div>
    <div class="divider">
      <span class="rule"></span>
      <span class="person-name">Marco Delgado</span>
      <span class="rule"></span>
    </div>
    <ul class="contact">
      <li>425-317-6084</li>
      <li>www.<span class="accent">brovanhs</span>.com</li>
      <li>www.friendlane.com/BrovanHomeServices</li>
      <li>www.picstream.com/BrovanHomeServices</li>
    </ul>
    <div class="base-band"></div>
  </section>

</main>
</body>
</html>
```